New Book Cover Design Project for book about Trade Blend

DetWe need a book cover (front, back, spine) for a new book entitled ‘Trade Blend’’ and subtitled “beyond old rules toward real buyer wishes” (inverted commas not to be part of the title and subtitle). The author is Malcolm Ferrisby. The publisher is Tessellane Insights. The finished size of the paperback version will be 5" x 8" (127 x 203.2 mm). There will be paperback, hardback, and e-book versions. The final number of pages is expected to be in the region of 80 pages. Text for the back cover is in an attached document. At the bottom of the back cover should be publisher logo (rectangular) on the left and space for the ISBN bar code on the right. The design should be original and not include any stock images that have been created by someone else or may require obtaining a copyright licence to use. Symbols in common use and not copyrighted are probably ok. There are no required images, photographs or symbols except the publisher logo at the left bottom of the back cover. Spine lettering should be UK/US style with the top of the writing nearest the front cover. The designer is free to be creative using appropriate diagrams, symbols or abstract designs. A copy of the publisher logo is attached. Designers are assured that when evaluating designs absolutely no notice whatsoever is taken of a designer's Pixel Forum ranking or status; We are completely output driven, so what matters is the design, not the ranking or status of the designer. In a similar way, designs are not evaluated as 'good' or 'bad' - the winning design will be chosen after review by a design review panel and is not decided arbitrarily by a single person. All submitted designs should be capable of effective copyright assignment. Designs submitted for consideration should include front cover, spine, and back cover.
Candidate Trade Blend words that can be included in designs, if the designer wishes, include: product, place, promotion, price, consumer, company objectives, participants, physical evidence, process of service assembly, battery life, usability, security, fashion, design, brand, appearance, health, obedience, sustainability, accessibility, value, idea, information operation, beliefs, vectors.

Target Market(s)

Academics, teachers, text book writers, and students concerned with marketing.

Industry/Entity Type

Education

Font styles to use
Serif

Requirements
Must have
• • Author on the front cover and the spine. Templates have been added to the brief for the cover with spine for a 80 page book. There are .indd and .pdf templates that can be used. the .indd and .pdf templates show where the ISBN blocks should go. The other .PDF templates have the ISBN in the wrong place (middle of the lower back cover) but have more information about the meanings of template markings. Bleeds - PLEASE NOTE - the cover printing is not exact - there is minor variation when the printers print the covers. Therefore do not have solid blocks of colour that go to the edges of the spine or spine and cover pages with different blocks of colour - solid blocks of colour may go round the spine folds a little bit! See the templates - they indicate the areas for possible printing imprecision. The ISBN numbers in the template file names are what will be used - perfect is for the paperback and case is for the hardback.
Nice to have
• • It is not necessary to have the subtitle on the spine. The final book size may not be 80 pages, therefore the spine width may change, but not by much. • Use only standard fonts.
Should not have
• • Ideally, stock images should not be used as we cannot control other uses of images created by other sources, thus potentially damaging the book branding. I don't like solid black cover or spine backgrounds.

```html
<!DOCTYPE html>
<html lang="en">
<head>
<meta charset="utf-8">
<title>Trade Blend – Cover Spread</title>
<link rel="stylesheet" href="https://fonts.googleapis.com/css2?family=Oswald:wght@400;500;600;700&family=PT+Sans:wght@400;700&family=Varela+Round&family=Nunito:wght@400;900&display=swap">
<style>
  :root {
    --stage: #2b2b2b;
    --cover-yellow: #ffe000;
    --ink: #3a3a3a;
    --paper: #ffffff;
    --publisher-blue: #1b5fb0;
  }
  * { margin: 0; padding: 0; box-sizing: border-box; }
  html, body {
    width: 982px; height: 1200px; overflow: hidden;
    background: var(--stage);
  }
  .cover-spread {
    position: absolute; left: 21px; top: 228px;
    width: 940px; height: 743px;
    background: var(--cover-yellow);
    color: var(--ink);
  }
  .headline-layer { position: absolute; inset: 0; }
  .back-subtitle {
    position: absolute; left: 45px; width: 386px; top: 134px;
    text-align: center; color: var(--paper);
    font: 15.5px/1.2 "Varela Round", sans-serif;
  }
  .back-blurb {
    position: absolute; left: 45px; top: 178px; width: 386px;
    font: 11.3px/17.5px "PT Sans", sans-serif;
    text-align: justify; text-align-last: center;
  }
  .about-author {
    position: absolute; left: 45px; top: 496px; width: 380px;
    font: 11.3px/17.5px "PT Sans", sans-serif;
  }
  .about-author h2 { font-size: 12.5px; font-weight: 700; }
  .publisher-mark {
    position: absolute; left: 45px; top: 653px;
    display: flex; align-items: center; gap: 8px;
    font: 700 17px/1 "PT Sans", sans-serif;
    color: var(--publisher-blue);
  }
  .publisher-mark .square {
    width: 14px; height: 14px; background: var(--publisher-blue);
  }
  .isbn-space {
    position: absolute; left: 257px; top: 601px;
    width: 181px; height: 109px; background: var(--paper);
  }
  .spine-text {
    position: absolute; left: 460px;
    writing-mode: vertical-rl;
    font: 600 14px/16px "Oswald", sans-serif;
    letter-spacing: 1.5px;
  }
  .spine-title { top: 51px; }
  .spine-author { top: 588px; }
</style>
</head>
<body>
  <main class="cover-spread">
    <svg class="headline-layer" viewBox="0 0 940 743" width="940" height="743">
      <!-- back cover title -->
      <text class="back-title" x="98" y="126" font-family="Oswald, sans-serif" font-size="57" font-weight="400" fill="#3a3a3a" textLength="279" lengthAdjust="spacingAndGlyphs">TRADE BLEND</text>

      <!-- front cover title -->
      <text class="front-title-top" x="501" y="150" font-family="Oswald, sans-serif" font-size="88" font-weight="400" fill="#3a3a3a" textLength="319" lengthAdjust="spacingAndGlyphs">TRADE</text>
      <text class="front-title-main" x="502" y="409" font-family="Oswald, sans-serif" font-size="320" font-weight="700" fill="#3a3a3a" textLength="365" lengthAdjust="spacingAndGlyphs">BLEND</text>

      <rect class="loudhailer-art" x="826" y="40" width="80" height="110" rx="8" fill="#3a3a3a" role="img" aria-label="Illustration of a loudhailer sounding out from the title"/>

      <!-- front subtitle -->
      <g class="front-subtitle" transform="rotate(-6 703 520)" fill="#ffffff" text-anchor="middle">
        <text x="703" y="462" font-family="Nunito, sans-serif" font-size="29" font-weight="400">Beyond Old</text>
        <text x="703" y="496" font-family="Nunito, sans-serif" font-size="29" font-weight="400">Rules Toward</text>
        <text x="703" y="530" font-family="Nunito, sans-serif" font-size="29" font-weight="400">Real</text>
        <text x="703" y="566" font-family="Nunito, sans-serif" font-size="31" font-weight="900">Buyer</text>
        <text x="703" y="598" font-family="Nunito, sans-serif" font-size="31" font-weight="900">Wishes</text>
      </g>

      <!-- front author -->
      <text class="front-author" x="507" y="683" font-family="Oswald, sans-serif" font-size="57" font-weight="500" fill="#3a3a3a" textLength="396" lengthAdjust="spacingAndGlyphs">MALCOLM FERRISBY</text>
    </svg>

    <p class="back-subtitle">Beyond Old Rules Toward Real Buyer Wishes</p>

    <p class="back-blurb">This book has been inspired by the many textbooks, classes and student work about trade blend, which simply present or teach trade blend as 4Ps - very often not even acknowledging where those 4Ps came from. This approach is simply unacceptable academic work - no discussion of the extensive research from the 1920s onwards, about what is needed for effective marketing and trade blend. In several ways, this is a thoroughly radical book pushing against the common approach of simply teaching about simplistic 4Ps. Many students produce a trade blend for a company; they shouldn't. The book provides a solid example of what academics often call 'critical thinking'. Other ways in which the book is radical, is that it shows that trade blend is not only for products and services; it is also for ideas. The book discusses the idea that marketing can be seen as a branch of information warfare. Positioning should be included in trade blend considerations. Trade blend should not only be considered for legitimate products, services, and ideas; it is relevant also for those who trade in legal or mixed legal and illegal products and services. Examples are explored in the book.</p>

    <section class="about-author">
      <h2>About the Author:</h2>
      <p>Malcolm Ferrisby has extensive experience in industry, academia, and a variety of NGOs working in human and civil rights. Within those contexts, he has a lot of marketing experience as practitioner, academic, and external examiner – contributing to the radical nature of this book.</p>
    </section>

    <div class="publisher-mark"><span class="square"></span><span>Tessellane Insights</span></div>
    <div class="isbn-space"></div>

    <span class="spine-text spine-title">TRADE BLEND</span>
    <span class="spine-text spine-author">MALCOLM FERRISBY</span>
  </main>
</body>
</html>
```